Small Business Broker Business Card Design

A business card design for a small business brokerage, which is a financial service, not unlike real estate brokerage, but for small businesses such as laundromats, pizza shops, restaurants, cleaners etc. The designs should all be simple, more conservative in nature, using the colors and font of the logo. Again, think real estate Brokerage as a business context
Contact Information for Business Card
Name: Glen R. Harlow. Title: Small Business Advisor. Email: g.harlow@bayfieldcapitalworks.example. Mobile: (555) 274-3918. Office: (555) 806-2147. www.bayfieldcapitalworks.example

```html
<!DOCTYPE html>
<html lang="en">
<head>
<meta charset="utf-8">
<title>Bayfield Capital Works — Business Card</title>
<link rel="stylesheet" href="https://fonts.googleapis.com/css2?family=Montserrat:wght@500;600;700;800&family=Arimo:wght@400;700&display=swap">
<style>
  :root {
    --stage: #111214;
    --navy: #142c5e;
    --navy-deep: #0f2250;
    --navy-light: #1f3f7a;
    --green: #6cc04a;
    --white: #ffffff;
  }
  * { box-sizing: border-box; margin: 0; padding: 0; }
  html, body {
    width: 1200px; height: 963px; overflow: hidden;
    background: var(--stage);
  }
  .canvas {
    width: 1200px; height: 963px;
    display: flex; flex-direction: column; align-items: center; justify-content: center;
    gap: 60px;
  }
  .card {
    position: relative;
    width: 700px; height: 400px;
    border-radius: 22px;
    overflow: hidden;
    background: linear-gradient(135deg, var(--navy-deep), var(--navy) 55%, #17326a);
    color: var(--white);
  }

  /* Front */
  .card-front { display: flex; align-items: center; }
  .brand {
    width: 372px; flex: none; padding-left: 36px; padding-right: 12px;
    display: flex; flex-direction: column; align-items: flex-start;
  }
  .brand-name {
    font-family: "Montserrat", sans-serif; font-weight: 800;
    font-size: 15px; letter-spacing: 1.2px; text-transform: uppercase;
    color: var(--white); white-space: nowrap;
  }
  .brand-tagline {
    margin-top: 6px;
    font-family: "Montserrat", sans-serif; font-weight: 600;
    font-size: 7.6px; letter-spacing: 1.5px; text-transform: uppercase;
    color: var(--green); white-space: nowrap;
  }
  .brand-mark {
    width: 14px; height: 14px; background: var(--green); margin-bottom: 14px;
  }
  .divider {
    width: 1.5px; height: 190px; flex: none; background: var(--green); margin: 0 26px 0 14px;
  }
  .contact { flex: 1; min-width: 0; padding-right: 16px; }
  .person-name {
    font-family: "Montserrat", sans-serif; font-weight: 800;
    font-size: 25px; letter-spacing: 1px; text-transform: uppercase;
    white-space: nowrap;
  }
  .person-title {
    margin-top: 2px;
    font-family: "Arimo", sans-serif; font-size: 15px; color: var(--green);
  }
  .contact-list { list-style: none; margin-top: 16px; }
  .contact-list li {
    display: flex; align-items: center; gap: 9px;
    font-family: "Arimo", sans-serif; font-size: 13px; line-height: 24px;
    white-space: nowrap;
  }
  .contact-list svg { width: 13px; height: 13px; flex: none; }

  /* Back */
  .card-back .pattern {
    position: absolute; inset: 0;
    background: radial-gradient(ellipse at 70% 80%, var(--navy-light), var(--navy) 60%, var(--navy-deep));
  }
  .card-back .brand-center {
    position: absolute; inset: 0;
    display: flex; flex-direction: column; align-items: center; justify-content: center;
  }
  .card-back .brand-name { font-size: 24px; letter-spacing: 2.4px; }
  .card-back .brand-tagline { font-size: 11px; letter-spacing: 2.4px; margin-top: 8px; }
  .card-back .brand-mark { width: 20px; height: 20px; margin-bottom: 18px; }
</style>
</head>
<body>
<main class="canvas">

  <section class="card card-front" aria-label="Business card front">
    <div class="brand">
      <span class="brand-mark"></span>
      <p class="brand-name">Bayfield Capital Works, Inc</p>
      <p class="brand-tagline">Confidently buy or sell a local business today</p>
    </div>
    <span class="divider"></span>
    <div class="contact">
      <h1 class="person-name">Glen R. Harlow</h1>
      <p class="person-title">Small Business Advisor</p>
      <ul class="contact-list">
        <li>
          <svg viewBox="0 0 16 16" fill="none" stroke="var(--green)" stroke-width="1.5"><path d="M3 2h3l1.5 3.5-2 1.2a8 8 0 0 0 3.8 3.8l1.2-2L14 10v3a1 1 0 0 1-1 1A11 11 0 0 1 2 3a1 1 0 0 1 1-1z"/></svg>
          (555) 806-2147
        </li>
        <li>
          <svg viewBox="0 0 16 16" fill="none" stroke="var(--green)" stroke-width="1.5"><rect x="4" y="1.5" width="8" height="13" rx="1.5"/><path d="M7 12.2h2"/></svg>
          (555) 274-3918
        </li>
        <li>
          <svg viewBox="0 0 16 16" fill="none" stroke="var(--green)" stroke-width="1.5"><rect x="1.5" y="3.5" width="13" height="9" rx="1"/><path d="M1.5 4l6.5 5 6.5-5"/></svg>
          g.harlow@bayfieldcapitalworks.example
        </li>
        <li>
          <svg viewBox="0 0 16 16" fill="none" stroke="var(--green)" stroke-width="1.3"><circle cx="8" cy="8" r="6.5"/><ellipse cx="8" cy="8" rx="3" ry="6.5"/><path d="M1.5 8h13M2.5 5h11M2.5 11h11"/></svg>
          www.bayfieldcapitalworks.example
        </li>
      </ul>
    </div>
  </section>

  <section class="card card-back" aria-label="Business card back">
    <div class="pattern" role="img" aria-label="Embossed tonal pattern of repeating brand motifs across the card"></div>
    <div class="brand-center">
      <span class="brand-mark"></span>
      <p class="brand-name">Bayfield Capital Works, Inc</p>
      <p class="brand-tagline">Confidently buy or sell a local business today</p>
    </div>
  </section>

</main>
</body>
</html>
```